Web design project for exciting Australian start-up

Background
We are looking for a creative and talented web design artist to work alongside our market leading web developer.
• You will be required to create a modern and clean design theme for our website, incorporating selected rustic colour scheme elements for our exciting Australian start-up to operate within the coffee industry.
reoccurring work to be expected to flow to the successful designer.
Requirements
• c. 5 - 10 page website
• Landing page
• Log in/ out
• 404 template
• Typography is emphasised
• Please use either a) typemarrow.com, b) free web fonts, c) brindle fonts
• All design elements in vector format
• Preferably with icons for each header title(i.e. about us, how it works etc) but designer have free reign over how the site looks, so might not be applicable
• All pages to be responsive
• Down to eSlab resolution

High level visual design brief attached - additional pages to be worked from base design.

Design inspiration
• We would like to use design elements from the following sources:
http://www.zandrix.com/halcyon/ (Functionality)
Colour scheme refer to logo and complementary style guide

```html
<!DOCTYPE html>
<html lang="en">
<head>
<meta charset="utf-8">
<title>Bean Harbour — Online Coffee Market Place</title>
<link rel="stylesheet" href="https://fonts.googleapis.com/css2?family=Roboto+Condensed:wght@300;400;700&family=Lato:wght@300;400&display=swap">
<style>
  :root {
    --ink: #111111;
    --ink-soft: #444444;
    --nav-text: #666666;
    --orange: #f7952e;
    --hessian-light: #efe8dc;
    --hessian-mid: #ddd0bb;
    --bean-brown: #a8826a;
    --footer-bg: #e8e8e8;
    --footer-text: #555555;
    --white: #ffffff;
  }
  * { box-sizing: border-box; margin: 0; padding: 0; }
  html, body { width: 1200px; height: 988px; overflow: hidden; background: var(--white); }
  body { position: relative; font-family: "Lato", sans-serif; color: var(--ink); }

  .site-header { position: absolute; left: 0; top: 0; width: 1200px; height: 83px; background: var(--white); }
  .brand { position: absolute; left: 51px; top: 24px; display: flex; align-items: center; gap: 8px;
    font-family: "Roboto Condensed", sans-serif; font-weight: 700; font-size: 22px; letter-spacing: 1px; color: #2b2b2b; }
  .brand-dot { width: 34px; height: 34px; border-radius: 50%; background: var(--orange); }
  .main-nav { position: absolute; right: 53px; top: 28px; display: flex; align-items: center; gap: 33px;
    font-family: "Lato", sans-serif; font-size: 13px; color: var(--nav-text); }
  .login-btn { display: flex; align-items: center; gap: 7px; background: var(--ink); color: var(--white);
    padding: 0 14px; height: 29px; border-radius: 2px; font-size: 13px; }

  .hero { position: absolute; left: 0; top: 83px; width: 1200px; height: 707px;
    background: linear-gradient(180deg, var(--hessian-light) 0%, #f1ebe1 55%, var(--hessian-mid) 75%, var(--bean-brown) 100%); }
  .hero-photo { position: absolute; left: 590px; top: 95px; width: 540px; height: 540px;
    background: radial-gradient(ellipse at 50% 45%, #d9cfbf 0%, #e6ddcf 55%, rgba(239,232,220,0) 72%); }
  .hero-title { position: absolute; left: 86px; top: 150px; font-family: "Roboto Condensed", sans-serif; line-height: 1; }
  .hero-title .line-1 { display: block; font-weight: 300; font-size: 55px; color: var(--ink-soft); letter-spacing: -2px; }
  .hero-title .line-2 { display: block; font-weight: 700; font-size: 74px; color: var(--orange); margin-top: 2px; }
  .hero-title .line-3 { display: block; font-weight: 700; font-size: 64px; color: var(--ink); margin-top: 0; letter-spacing: -1px; }
  .watch-btn { position: absolute; left: 87px; top: 362px; width: 188px; height: 42px;
    border: 1px solid #b9b3a9; background: rgba(255,255,255,0.35); display: flex; align-items: center; gap: 18px; padding-left: 24px;
    font-family: "Roboto Condensed", sans-serif; font-weight: 700; font-size: 20px; color: #333333; }

  .site-footer { position: absolute; left: 0; top: 790px; width: 1200px; height: 198px; background: var(--footer-bg); color: var(--footer-text); }
  .footer-col { position: absolute; top: 34px; }
  .footer-col h3 { font-family: "Lato", sans-serif; font-weight: 400; font-size: 14px; color: var(--ink); margin-bottom: 12px; }
  .footer-col p { font-weight: 300; font-size: 12px; line-height: 16.6px; width: 310px; }
  .footer-col ul { list-style: none; font-size: 13.5px; line-height: 20px; font-weight: 300; color: #333; }
  .social li { display: flex; align-items: center; gap: 9px; line-height: 27px; }
  .social-dot { width: 17px; height: 17px; border-radius: 50%; background: #9a9a9a; }
  .footer-brand { position: absolute; left: 962px; top: 62px; text-align: center; }
  .footer-brand .name { display: flex; align-items: center; gap: 8px; justify-content: center;
    font-family: "Roboto Condensed", sans-serif; font-weight: 700; font-size: 20px; letter-spacing: 1px; color: #666; }
  .footer-brand .name .brand-dot { width: 28px; height: 28px; background: #8d8d8d; }
  .copyright { margin-top: 14px; font-size: 13px; color: #444; }
</style>
</head>
<body>
  <header class="site-header">
    <div class="brand"><span>BEAN</span><span class="brand-dot"></span><span>HARBOUR</span></div>
    <nav class="main-nav">
      <span>HOME</span><span>ABOUT US</span><span>HOW IT WORKS</span>
      <span class="login-btn">
        <svg width="12" height="13" viewBox="0 0 12 13"><circle cx="6" cy="3.5" r="3.2" fill="#fff"/><path d="M0 13c0-4 2.7-5.5 6-5.5s6 1.5 6 5.5z" fill="#fff"/></svg>
        LOGIN
      </span>
    </nav>
  </header>

  <section class="hero">
    <div class="hero-photo" role="img" aria-label="Hessian sack filled with roasted coffee beans"></div>
    <div role="img" aria-label="Row of roasted coffee beans along the bottom of the hessian backdrop" style="position:absolute;left:0;bottom:0;width:1200px;height:180px;background:linear-gradient(180deg,rgba(168,130,106,0) 0%,rgba(168,130,106,0.55) 100%);"></div>
    <h1 class="hero-title">
      <span class="line-1">AUSTRALIA’S FIRST</span>
      <span class="line-2">ONLINE COFFEE</span>
      <span class="line-3">MARKET PLACE</span>
    </h1>
    <div class="watch-btn">
      <svg width="13" height="15" viewBox="0 0 13 15"><path d="M0 0l13 7.5L0 15z" fill="#f7952e"/></svg>
      WATCH VIDEO
    </div>
  </section>

  <footer class="site-footer">
    <div class="footer-col" style="left:51px">
      <h3>ABOUT US</h3>
      <p>Lorem ipsum dolor sit amet, consectetur adipisicing elit, sed do eiusmod tempor incididunt ut labore et dolore magna aliqua. Ut enim ad minim veniam, quis nostrud exercitation ullamco laboris nisi ut aliquip ex ea commodo consequat. Duis aute irure dolor in reprehenderit in voluptate velit esse cillum dolore eu fugiat nulla pariatur.</p>
    </div>
    <div class="footer-col" style="left:429px">
      <h3>HELPFUL INFO</h3>
      <ul><li>About us</li><li>Media Enquiries</li><li>Terms &amp; Conditions</li><li>Privacy Policy</li></ul>
    </div>
    <div class="footer-col" style="left:618px">
      <h3>WHO WE ARE</h3>
      <ul><li>How It Works</li><li>Faq</li><li>Contact Us</li></ul>
    </div>
    <div class="footer-col" style="left:788px">
      <h3>FOLLOW US</h3>
      <ul class="social">
        <li><span class="social-dot"></span>Gatherly</li>
        <li><span class="social-dot"></span>Workweave</li>
        <li><span class="social-dot"></span>Gatherly</li>
        <li><span class="social-dot"></span>Workweave</li>
      </ul>
    </div>
    <div class="footer-brand">
      <div class="name"><span>BEAN</span><span class="brand-dot"></span><span>HARBOUR</span></div>
      <div class="copyright">Copyright © 2014 Bean Harbour.</div>
    </div>
  </footer>
</body>
</html>
```